Quanbrook Limited needs a business card design

We need a business card design that reflects both professionalism and innovation and captures our brand identity. We provide online enterprise solutions to HR and executive management. We would like to use the colors in our logo (Blue and Orange). See attached file.

We would like a more creative design than the existing attached business card but maintain the same information on it.

To see our products site, please visit www.quanbrook.example which reflects more our identity
Updates

Please see our site: www.quanbrook.example, not www.quanbrook.example.uk for our colors and look and feel

Target Market(s)

Senior Executives

Industry/Entity Type

Business

Requirements
Must have
• Logo and use of logo colors
Nice to have
• Icons
Should not have
• Images

```html
<!DOCTYPE html>
<html lang="en">
<head>
<meta charset="utf-8">
<title>Quanbrook Limited – Business Card</title>
<link href="https://fonts.googleapis.com/css2?family=Exo+2:wght@400;600&display=swap" rel="stylesheet">
<style>
  :root {
    --backdrop: #2a2a2c;
    --card: #ffffff;
    --brand-blue: #1a4fc4;
    --brand-orange: #e2531b;
    --ink: #1d1d1f;
  }
  * { box-sizing: border-box; margin: 0; padding: 0; }
  html, body {
    width: 1200px; height: 754px; overflow: hidden;
    background: var(--backdrop);
    font-family: "Exo 2", sans-serif;
  }
  .canvas { position: relative; width: 1200px; height: 754px; }
  .card {
    position: absolute; top: 212px;
    width: 540px; height: 330px;
    background: var(--card);
  }
  .card--front { left: 45px; }
  .card--back { left: 615px; }

  .company-name {
    position: absolute; white-space: nowrap;
    color: var(--brand-blue); font-weight: 600; line-height: 1;
    letter-spacing: 0.5px;
  }
  .card--front .company-name { left: 36px; top: 244px; font-size: 34px; }
  .card--back .company-name {
    left: 50%; top: 50%; transform: translate(-50%, -50%);
    font-size: 68px;
  }

  .identity {
    position: absolute; left: 250px; top: 48px; text-align: center;
  }
  .identity__name {
    color: var(--brand-blue); font-weight: 600; font-size: 17px;
    letter-spacing: 1px; text-transform: uppercase;
  }
  .identity__title {
    color: var(--ink); font-size: 11px; letter-spacing: 1px;
    text-transform: uppercase;
  }
  .contacts { position: absolute; left: 236px; top: 108px; list-style: none; }
  .contacts li, .address {
    display: flex; align-items: center; gap: 7px; white-space: nowrap;
    color: var(--ink); font-size: 12.5px; letter-spacing: 0.5px;
    margin-bottom: 6px;
  }
  .icon { width: 14px; height: 14px; flex: none; }
  .divider {
    position: absolute; left: 262px; top: 246px;
    width: 200px; height: 1.5px; background: var(--brand-orange);
  }
  .address { position: absolute; left: 262px; top: 264px; }
</style>
</head>
<body>
<main class="canvas">
  <section class="card card--front" aria-label="Card front">
    <div class="identity">
      <p class="identity__name">Daniel Hartley</p>
      <p class="identity__title">General Manager</p>
    </div>
    <ul class="contacts">
      <li>
        <svg class="icon" viewBox="0 0 16 16"><circle cx="8" cy="8" r="8" fill="#1a4fc4"/><path d="M5.2 4.2l1.4-.2.8 1.9-.9.7a5 5 0 0 0 2.9 2.9l.7-.9 1.9.8-.2 1.4c-3.7.3-7-3-6.6-6.6z" fill="#fff"/></svg>
        020 555 0143
      </li>
      <li>
        <svg class="icon" viewBox="0 0 16 16"><circle cx="8" cy="8" r="8" fill="#1a4fc4"/><rect x="4" y="5" width="8" height="6" rx="0.8" fill="#fff"/><path d="M4.3 5.4L8 8.2l3.7-2.8" stroke="#1a4fc4" stroke-width="0.9" fill="none"/></svg>
        d.hartley@quanbrook.example
      </li>
      <li>
        <svg class="icon" viewBox="0 0 16 16"><circle cx="8" cy="8" r="8" fill="#1a4fc4"/><circle cx="8" cy="8" r="4" stroke="#fff" stroke-width="1" fill="none"/><path d="M4 8h8M8 4c-2 2.5-2 5.5 0 8M8 4c2 2.5 2 5.5 0 8" stroke="#fff" stroke-width="0.8" fill="none"/></svg>
        www.quanbrook.example
      </li>
    </ul>
    <p class="company-name">Quanbrook</p>
    <div class="divider"></div>
    <p class="address">
      <svg class="icon" viewBox="0 0 16 16"><circle cx="8" cy="8" r="8" fill="#1a4fc4"/><path d="M8 3.5a3 3 0 0 0-3 3c0 2.2 3 6 3 6s3-3.8 3-6a3 3 0 0 0-3-3z" fill="#fff"/><circle cx="8" cy="6.5" r="1.1" fill="#1a4fc4"/></svg>
      47 Ashgrove Lane, Level 6, Brookfield
    </p>
  </section>

  <section class="card card--back" aria-label="Card back">
    <p class="company-name">Quanbrook</p>
  </section>
</main>
</body>
</html>
```